Stylish Business Cards Wanted

- DOUBLE SIDED Design Required -

High end, edgy cards for a corporate and personal stylist. Must include logo,
Name: Belinda Harwick
Title: Director and Stylist
telephone : +61 8 7142 5809
email: belinda@theloombriefing.example
website: theloombriefing.example
Tag: Corporate Workwear & Uniform Specialist | Personal Stylist
Would like nice icons for telephone, email, website

Target Market(s)

Businesses wanting stylish uniforms, people wanting stylish wardrobes

Industry/Entity Type

Corporate Workwear Stylist

Contact Information for Business Card

I would like black, white and gold foiling incorporated in the design - possibly a touch of the other colours on my branding guide attached Name: Belinda Harwick Title: Director and Stylist telephone : +61 8 7142 5809 email: belinda@theloombriefing.example website: theloombriefing.example Tag: Corporate Workwear & Uniform Specialist | Personal Stylist Would like nice icons for telephone, email, website

Font styles to use
Other font styles liked:
• Raleway

Colors

Designer to choose colors to be used in the design.

Requirements
Must have
• Gold foil accents

```html
<!DOCTYPE html>
<html lang="en">
<head>
<meta charset="utf-8">
<title>The Loom Briefing – Business Cards</title>
<link rel="stylesheet" href="https://fonts.googleapis.com/css2?family=Montserrat:wght@500;600&family=Arimo&display=swap">
<style>
  :root {
    --backdrop: #e3e3e3;
    --card: #ffffff;
    --ink: #111111;
    --gold: #e5b94e;
    --grey-text: #333333;
  }
  * { box-sizing: border-box; margin: 0; padding: 0; }
  html, body { width: 1200px; height: 900px; overflow: hidden; }
  body {
    background: var(--backdrop);
    position: relative;
    font-family: "Arimo", Arial, sans-serif;
  }
  .card {
    position: absolute;
    left: 270px;
    width: 660px;
    height: 377px;
    background: var(--card);
    box-shadow: 0 6px 18px rgba(0,0,0,0.18);
    overflow: hidden;
  }
  .card--front { top: 52px; }
  .card--back { top: 470px; }

  .brand-name {
    font-family: "Montserrat", Arial, sans-serif;
    font-weight: 600;
    color: var(--ink);
    letter-spacing: 0.04em;
    display: flex;
    align-items: center;
    gap: 12px;
    white-space: nowrap;
  }
  .brand-name__mark {
    width: 18px;
    height: 18px;
    background: var(--gold);
    flex: none;
  }
  .card--front .brand-name {
    position: absolute;
    left: 50%;
    top: 50%;
    transform: translate(-50%, -50%);
    font-size: 38px;
  }
  .card--back .brand-name {
    position: absolute;
    left: 42px;
    top: 92px;
    font-size: 28px;
  }

  .contact-block {
    position: absolute;
    right: 34px;
    top: 38px;
    text-align: right;
  }
  .contact-block__accent {
    position: absolute;
    right: 0;
    top: 40px;
    width: 6px;
    height: 38px;
    background: var(--gold);
    border-radius: 3px 0 0 3px;
  }
  .person-name {
    font-family: "Montserrat", Arial, sans-serif;
    font-weight: 600;
    font-size: 24px;
    color: var(--gold);
    line-height: 1;
  }
  .person-title {
    font-size: 13px;
    color: var(--grey-text);
    margin-top: 3px;
  }
  .contact-icons {
    display: flex;
    justify-content: flex-end;
    gap: 16px;
    margin-top: 34px;
  }
  .contact-icons svg { width: 22px; height: 22px; display: block; }
  .contact-lines {
    list-style: none;
    margin-top: 10px;
    font-size: 15px;
    color: var(--ink);
    line-height: 1.35;
  }

  .tagline-band {
    position: absolute;
    left: 0;
    right: 0;
    bottom: 44px;
    height: 34px;
    background: var(--ink);
    color: var(--gold);
    font-family: "Montserrat", Arial, sans-serif;
    font-weight: 500;
    font-size: 15px;
    letter-spacing: 0.02em;
    display: flex;
    align-items: center;
    justify-content: center;
    gap: 10px;
  }
  .tagline-band__divider { color: var(--card); }
  .gold-stripe {
    position: absolute;
    left: 0;
    right: 0;
    bottom: 18px;
    height: 18px;
    background: var(--gold);
  }
</style>
</head>
<body>

<section class="card card--front" aria-label="Business card front">
  <div class="brand-name"><span class="brand-name__mark"></span>The Loom Briefing</div>
</section>

<section class="card card--back" aria-label="Business card back">
  <div class="brand-name"><span class="brand-name__mark"></span>The Loom Briefing</div>

  <div class="contact-block">
    <p class="person-name">Belinda Harwick</p>
    <p class="person-title">Director and Stylist</p>

    <div class="contact-icons">
      <svg viewBox="0 0 24 24" aria-label="Phone" role="img">
        <circle cx="12" cy="12" r="12" fill="var(--ink)"/>
        <path d="M8.5 6.5l2 0 1 3-1.4 1a7 7 0 0 0 3.4 3.4l1-1.4 3 1v2c0 .8-.7 1.4-1.5 1.3A10 10 0 0 1 7.2 8c-.1-.8.5-1.5 1.3-1.5z" fill="#fff"/>
      </svg>
      <svg viewBox="0 0 24 24" aria-label="Email" role="img">
        <circle cx="12" cy="12" r="12" fill="var(--ink)"/>
        <rect x="6" y="8" width="12" height="8.5" rx="1" fill="#fff"/>
        <path d="M6.3 8.4L12 13l5.7-4.6" stroke="var(--ink)" stroke-width="1.2" fill="none"/>
      </svg>
      <svg viewBox="0 0 24 24" aria-label="Website" role="img">
        <circle cx="12" cy="12" r="12" fill="var(--ink)"/>
        <circle cx="12" cy="12" r="6" fill="none" stroke="#fff" stroke-width="1.3"/>
        <ellipse cx="12" cy="12" rx="2.6" ry="6" fill="none" stroke="#fff" stroke-width="1.1"/>
        <path d="M6 12h12" stroke="#fff" stroke-width="1.1"/>
      </svg>
    </div>

    <ul class="contact-lines">
      <li>+61 8 7142 5809</li>
      <li>belinda@theloombriefing.example</li>
      <li>theloombriefing.example</li>
    </ul>
    <span class="contact-block__accent"></span>
  </div>

  <div class="tagline-band">
    <span>CORPORATE WORKWEAR</span>
    <span class="tagline-band__divider">|</span>
    <span>UNIFORM SPECIALIST</span>
    <span class="tagline-band__divider">|</span>
    <span>PERSONAL STYLIST</span>
  </div>
  <div class="gold-stripe"></div>
</section>

</body>
</html>
```